Clear Plastic Card Design

I am looking to have a business card designed from my logo icon. I am looking to match the style of a different business card I have attached in the files.
Looking for a card that is plastic, with layers of transparency in the shape of my logo icon (also attached in the files) - not a circle like the other card. The winning design will incorporate the red icon logo on the front and back and include the charity's name, "Light for the Weary Souls" in the same or similar font, as well as an email and phone number. For now, use the email: email@lightfortheweary-mail.org and the phone number 555-382-7194.
We like how the sample business card has transparency, partial and full opacity layers and a matching color scheme. Files will need to be in vector so that our business card printing company can work with it.
UPDATE:
We've some excellent designs in, thank you everyone! I got an early review from the owner, and he requested a minor redirect to find his perfect design. He wants the design to stand out by NOT being a rectangle. Try instead a circle, square, or best yet - something that falls in the outline of the logo icon, either fully or partially. Thank you, everyone!
Light for the Weary Souls text should be incorporated as well as a phone and email.

```html
<!DOCTYPE html>
<html lang="en">
<head>
<meta charset="UTF-8">
<title>Light for the Weary Souls – Clear Business Card</title>
<link href="https://fonts.googleapis.com/css2?family=Outfit:wght@400;700&family=Roboto:wght@400;700&display=swap" rel="stylesheet">
<style>
  :root {
    --backdrop: #e8e5e2;
    --card-clear: #f1f0f0;
    --card-frost: #d9d4d1;
    --card-edge: #c9c6c6;
    --red-light: #d45050;
    --red-mid: #c0222a;
    --red-deep: #95000f;
    --ink: #2b2b2b;
    --white: #ffffff;
  }
  * { margin: 0; padding: 0; box-sizing: border-box; }
  html, body {
    width: 1200px; height: 836px; overflow: hidden;
    background: var(--backdrop);
  }
  .canvas { position: relative; width: 1200px; height: 836px; }
  .card-shape { position: absolute; left: 0; top: 0; }

  .contact-block {
    position: absolute; left: 78px; top: 200px; width: 424px;
    text-align: right; color: var(--white);
    font-family: "Roboto", Arial, sans-serif;
  }
  .person-name { font-weight: 700; font-size: 34px; letter-spacing: 0.5px; line-height: 1; margin-top: 50px; }
  .person-role { font-size: 20px; margin-top: 6px; }
  .contact-list { list-style: none; margin-top: 26px; font-size: 18px; line-height: 32px; }
  .contact-list li { display: flex; justify-content: flex-end; align-items: center; gap: 10px; }
  .contact-list svg { width: 16px; height: 16px; flex: none; }

  .org-name {
    position: absolute; left: 206px; top: 498px;
    font-family: "Outfit", Arial, sans-serif; font-weight: 400;
    font-size: 70px; line-height: 74px; color: var(--ink);
  }
  .brand-mark {
    position: absolute; left: 570px; top: 210px; width: 520px;
    font-family: "Outfit", Arial, sans-serif; font-weight: 700;
    font-size: 118px; line-height: 120px; color: var(--red-mid);
    text-align: center;
  }
</style>
</head>
<body>
<div class="canvas">
  <svg class="card-shape" width="1200" height="836" viewBox="0 0 1200 836">
    <defs>
      <linearGradient id="cardFill" x1="0" x2="1" y1="0" y2="0">
        <stop offset="0" stop-color="var(--card-frost)"/>
        <stop offset="0.36" stop-color="var(--card-frost)"/>
        <stop offset="0.42" stop-color="var(--card-clear)"/>
        <stop offset="1" stop-color="var(--card-clear)"/>
      </linearGradient>
      <linearGradient id="bandFill" x1="0" x2="1" y1="0" y2="0">
        <stop offset="0" stop-color="var(--red-light)"/>
        <stop offset="0.6" stop-color="var(--red-mid)"/>
        <stop offset="1" stop-color="var(--red-deep)"/>
      </linearGradient>
    </defs>
    <path class="card-outline"
      d="M380 116 L870 116 Q898 116 904 144 L910 176 L1030 176 Q1122 176 1122 300 L1122 470 Q1122 568 1030 568 L912 568 L908 620 Q904 650 880 672 L840 708 Q826 720 806 720 L380 720 C190 720 78 600 78 418 C78 236 190 116 380 116 Z"
      fill="url(#cardFill)" stroke="var(--card-edge)" stroke-width="2"/>
    <path class="contact-band" d="M118 200 L536 200 L536 472 L82 472 C78 400 88 280 118 200 Z" fill="url(#bandFill)" opacity="0.92"/>
  </svg>

  <div class="contact-block">
    <p class="person-name">DANIEL REEVES</p>
    <p class="person-role">Founder &amp; CEO</p>
    <ul class="contact-list">
      <li>555-382-7194
        <svg viewBox="0 0 16 16" aria-hidden="true"><path d="M4 1.5 L6.5 4.5 L5 6.5 Q6.5 9.5 9.5 11 L11.5 9.5 L14.5 12 L13 14.5 Q6 14 1.5 3 Z" fill="none" stroke="currentColor" stroke-width="1.4"/></svg>
      </li>
      <li>email@lightfortheweary-mail.org
        <svg viewBox="0 0 16 16" aria-hidden="true"><rect x="1" y="3" width="14" height="10" fill="currentColor"/><path d="M1 3 L8 9 L15 3" fill="none" stroke="var(--red-mid)" stroke-width="1.2"/></svg>
      </li>
      <li>lightforthewearysouls.org
        <svg viewBox="0 0 16 16" aria-hidden="true"><circle cx="8" cy="8" r="6.5" fill="none" stroke="currentColor" stroke-width="1.4"/><path d="M1.5 8 H14.5 M8 1.5 Q4 8 8 14.5 M8 1.5 Q12 8 8 14.5" fill="none" stroke="currentColor" stroke-width="1.1"/></svg>
      </li>
    </ul>
  </div>

  <div class="brand-mark">Weary<br>Souls</div>

  <p class="org-name">Light for the<br>Weary Souls</p>
</div>
</body>
</html>
```